National Mission Critical Construction Contractor needs Stationery Design to make a bold statement

We are a small commercial construction company, working primarily in mission critical facilities across the U.S.. We have exciting corporate changes going an and a new logo and office space so we need new stationery. The final design should incorporate our new logo and invoke a fresh, high-tech feel while looking simple and modern.

Industry/Entity Type

Construction

Contact Information for Business Card

We are required to list our state licensing qualifications on the back of our card.

Font styles to use
Sans Serif

Requirements
Must have
• We need to have a design for second page of stationery, envelopes both standard and with a window and for a 3 x 4 notepad.

```html
<!DOCTYPE html>
<html lang="en">
<head>
<meta charset="utf-8">
<title>Northgate Construction Management – Business Card</title>
<link rel="stylesheet" href="https://fonts.googleapis.com/css2?family=Montserrat:wght@600&family=Nunito+Sans:wght@400;800&display=swap">
<style>
  :root {
    --page: #1c1c1c;
    --paper: #f2f2f1;
    --brand-blue: #1f5fae;
    --band-blue: #1d5ba8;
    --leaf-green: #78b52b;
    --rule-grey: #b9bcc0;
    --ink: #3a3a3a;
    --white: #ffffff;
  }
  html, body {
    margin: 0;
    width: 1200px;
    height: 1001px;
    overflow: hidden;
    background: var(--page);
  }
  .card {
    position: absolute;
    left: 306px;
    width: 588px;
    height: 329px;
    box-shadow: 0 3px 10px rgba(0,0,0,0.5);
  }
  .card--front { top: 133px; }
  .card--back { top: 539px; }
  .paper { fill: var(--paper); }
  .band { fill: var(--band-blue); }
  .stripe { fill: var(--leaf-green); }
  .emblem { fill: var(--white); }
  .wordmark-rule { stroke: var(--rule-grey); stroke-width: 1.5; }
  .wordmark {
    font-family: "Montserrat", sans-serif;
    font-weight: 600;
    fill: var(--brand-blue);
  }
  .wordmark__name { font-size: 31px; letter-spacing: 1px; }
  .wordmark__tag { font-size: 9.5px; letter-spacing: 2.6px; }
  .wordmark--large .wordmark__name { font-size: 34px; }
  .wordmark--large .wordmark__tag { font-size: 10.5px; letter-spacing: 2.6px; }
  .person-name {
    font-family: "Nunito Sans", sans-serif;
    font-weight: 800;
    font-size: 18px;
    fill: var(--brand-blue);
  }
  .person-role, .contact-text, .address-text {
    font-family: "Nunito Sans", sans-serif;
    font-weight: 400;
    font-size: 14px;
    fill: var(--ink);
  }
  .icon-tile { fill: var(--brand-blue); }
  .icon-glyph { fill: none; stroke: var(--white); stroke-width: 1.3; }
  .icon-fill { fill: var(--white); }
</style>
</head>
<body>

<svg class="card card--front" viewBox="0 0 588 329" aria-label="Business card front">
  <rect class="paper" width="588" height="329"/>
  <path class="band" d="M0 0 H588 V82 Q320 8 0 20 Z"/>
  <path class="stripe" d="M0 24 Q320 13 588 86 V89 Q320 24 0 33 Z"/>
  <circle class="emblem" cx="433" cy="70" r="40"/>

  <text class="wordmark" text-anchor="middle">
    <tspan class="wordmark__name" x="433" y="143">NORTHGATE</tspan>
  </text>
  <line class="wordmark-rule" x1="323" y1="150" x2="543" y2="150"/>
  <text class="wordmark" text-anchor="middle">
    <tspan class="wordmark__tag" x="433" y="163">CONSTRUCTION MANAGEMENT</tspan>
  </text>

  <text class="person-name" x="45" y="145">JORDAN ELLERY</text>
  <text class="person-role" x="45" y="165">General Manager</text>

  <g class="contact-list">
    <g class="contact-item contact-item--mobile">
      <rect class="icon-tile" x="45" y="221" width="15" height="15" rx="3"/>
      <rect class="icon-glyph" x="49.5" y="224" width="6" height="9" rx="1"/>
      <text class="contact-text" x="70" y="234">(202) 555-0148</text>
    </g>
    <g class="contact-item contact-item--phone">
      <rect class="icon-tile" x="45" y="239" width="15" height="15" rx="3"/>
      <path class="icon-fill" d="M49 242.5 l2.5-0.5 1.2 3 -1.4 1 q1.2 2.4 3.4 3.4 l1-1.4 3 1.2 -0.5 2.5 q-5.5 0.5 -9.2-9.2z"/>
      <text class="contact-text" x="70" y="252">(202) 555-0162</text>
    </g>
    <g class="contact-item contact-item--email">
      <rect class="icon-tile" x="45" y="257" width="15" height="15" rx="3"/>
      <rect class="icon-glyph" x="48" y="260.5" width="9" height="7"/>
      <path class="icon-glyph" d="M48 260.5 l4.5 4 4.5-4"/>
      <text class="contact-text" x="70" y="270">info@northgatecm.com</text>
    </g>
    <g class="contact-item contact-item--web">
      <rect class="icon-tile" x="45" y="276" width="15" height="15" rx="3"/>
      <circle class="icon-glyph" cx="52.5" cy="283.5" r="4.5"/>
      <ellipse class="icon-glyph" cx="52.5" cy="283.5" rx="2" ry="4.5"/>
      <path class="icon-glyph" d="M48 283.5 h9"/>
      <text class="contact-text" x="70" y="289">www.northgatecm.com</text>
    </g>
  </g>

  <text class="address-text" text-anchor="end">
    <tspan x="544" y="270">1820 Linden Avenue NW</tspan>
    <tspan x="544" y="289">Suite 210, Washington</tspan>
  </text>
</svg>

<svg class="card card--back" viewBox="0 0 588 329" aria-label="Business card back">
  <rect class="paper" width="588" height="329"/>
  <path class="band" d="M0 0 H588 V144 C520 138 430 134 320 135 C250 136 150 148 0 178 Z"/>
  <path class="stripe" d="M0 181 C150 151 250 139 320 138 C430 137 520 141 588 147 V155 C520 149 430 145 320 146 C250 147 150 158 0 184 Z"/>
  <circle class="emblem" cx="294" cy="145" r="47"/>

  <text class="wordmark wordmark--large" text-anchor="middle">
    <tspan class="wordmark__name" x="294" y="227">NORTHGATE</tspan>
  </text>
  <line class="wordmark-rule" x1="176" y1="234" x2="412" y2="234"/>
  <text class="wordmark wordmark--large" text-anchor="middle">
    <tspan class="wordmark__tag" x="294" y="248">CONSTRUCTION MANAGEMENT</tspan>
  </text>
</svg>

</body>
</html>
```